Film Production Company Needs HTML Website Design

My production company, QuillanStudioWorks.com , needs to have an HTML design of our website. I would like a minotaur as the company symbol, as well as a hellfire in the background. Something dark and edgy, like we currently have, but different. The password to open the attached zip file is: KTRW3mze81Pvd62JGsQe
Please check out our website and include all of the tabs that are currently in the design, especially the Investor section.

Film Production

```html
<!DOCTYPE html>
<html lang="en">
<head>
<meta charset="utf-8">
<title>Quillan Studio Works</title>
<link href="https://fonts.googleapis.com/css2?family=Cinzel:wght@400;700&family=Cormorant+Garamond:wght@500;600;700&family=Questrial&display=swap" rel="stylesheet">
<style>
  :root {
    --page: #ffffff;
    --ink: #000000;
    --ember: #3a0000;
    --ember-deep: #1c0000;
    --blood: #7a0a06;
    --glow: #a01208;
    --nav-red: #e0262a;
    --gold: #f0b418;
    --gold-deep: #d9891a;
    --cream: #f2d9b0;
    --field: #3d0000;
    --muted: #9a9a9a;
  }
  * { margin: 0; padding: 0; box-sizing: border-box; }
  html, body { width: 1200px; height: 1000px; overflow: hidden; background: var(--page); }
  .site {
    position: absolute; left: 50px; top: 37px; width: 1108px; height: 920px;
    background:
      radial-gradient(ellipse 420px 300px at 60px 250px, rgba(170,30,5,.55), transparent 70%),
      radial-gradient(ellipse 700px 420px at 560px 420px, rgba(90,0,0,.55), transparent 75%),
      linear-gradient(180deg, var(--ink) 0, var(--ink) 90px, var(--ember-deep) 150px, var(--ember) 420px, var(--ember-deep) 760px, var(--ink) 850px);
    box-shadow: 0 0 30px rgba(0,0,0,.25);
    overflow: hidden;
  }
  .brand { position: absolute; left: 0; width: 100%; top: 48px; text-align: center; font-family: "Cinzel", serif; font-weight: 700; color: var(--gold-deep); }
  .brand-name { font-size: 60px; letter-spacing: 1px; line-height: 1; }
  .brand-sub { font-size: 20px; letter-spacing: 20px; margin-top: 26px; line-height: 1; }
  .nav {
    position: absolute; left: 12px; top: 198px; width: 1086px; height: 52px;
    background: var(--ink); border: 3px solid var(--blood); border-radius: 10px;
    box-shadow: 0 0 10px var(--glow), inset 0 0 4px var(--glow);
  }
  .nav a {
    position: absolute; top: 10px; font-family: "Cinzel", serif; font-size: 18px;
    color: var(--nav-red); text-decoration: none; letter-spacing: .5px;
  }
  .nav a.contact { color: var(--gold); }
  .nav .sep { position: absolute; top: 10px; width: 1px; height: 24px; background: #444; }
  .panel {
    position: absolute; border: 3px solid var(--blood); border-radius: 8px;
    box-shadow: 0 0 12px var(--glow), inset 0 0 10px rgba(0,0,0,.6);
  }
  .panel.locations { left: 10px; top: 263px; width: 330px; height: 565px; background: linear-gradient(180deg, rgba(60,0,0,.4), rgba(20,0,0,.6)); }
  .panel.form { left: 777px; top: 268px; width: 312px; height: 335px; background: var(--ink); }
  .panel.info { left: 777px; top: 625px; width: 312px; height: 194px; background: var(--ink); }
  .heading { position: absolute; color: var(--gold); line-height: 1; }
  .heading.serif { font-family: "Cormorant Garamond", serif; font-weight: 700; font-size: 31px; letter-spacing: -1px; }
  .heading.caps { font-family: "Cinzel", serif; font-size: 28px; letter-spacing: 1px; }
  .address { position: absolute; left: 30px; top: 103px; font-family: "Cormorant Garamond", serif; font-weight: 600; font-size: 14px; line-height: 22px; color: var(--cream); }
  .map {
    position: absolute; left: 12px; top: 242px; width: 260px; height: 226px; border-radius: 22px;
    background: linear-gradient(180deg, #4a0000, #300000);
    border: 2px solid #5a3030; box-shadow: inset 0 2px 3px rgba(255,255,255,.15);
    display: flex; align-items: center; justify-content: center;
    font-family: "Cormorant Garamond", serif; font-size: 40px; color: var(--muted);
  }
  .hero {
    position: absolute; left: 360px; top: 265px; width: 350px; height: 580px;
    background:
      radial-gradient(ellipse 140px 250px at 50% 55%, #f6a21a, #d14a06 45%, #5a1000 75%, transparent 100%),
      var(--ink);
  }
  .label { font-family: "Questrial", sans-serif; font-size: 10px; color: var(--cream); position: absolute; letter-spacing: .5px; }
  .field { position: absolute; left: 18px; width: 260px; background: var(--field); }
  .btn {
    position: absolute; top: 282px; width: 66px; height: 14px; border-radius: 6px;
    background: linear-gradient(180deg, #c87a28, #6a2a06);
    font-family: "Questrial", sans-serif; font-size: 10px; color: var(--cream); text-align: center; line-height: 14px;
  }
  .info-text { position: absolute; left: 14px; top: 50px; font-family: "Questrial", sans-serif; font-size: 9.5px; line-height: 11.5px; color: var(--cream); }
  .info-text p + p { margin-top: 22px; }
  .social { position: absolute; left: 22px; top: 864px; display: flex; gap: 6px; }
  .social span {
    height: 28px; padding: 0 5px; background: #111; display: flex; align-items: center;
    font-family: "Questrial", sans-serif; font-size: 9px; color: #fff;
  }
  .footer { position: absolute; left: 462px; top: 873px; font-family: "Questrial", sans-serif; font-size: 10.5px; color: var(--gold-deep); }
</style>
</head>
<body>
<main class="site">
  <header class="brand">
    <div class="brand-name">QUILLAN STUDIO</div>
    <div class="brand-sub">WORKS</div>
  </header>

  <nav class="nav">
    <a style="left:108px">Home</a><span class="sep" style="left:203px"></span>
    <a style="left:240px">About Us</a><span class="sep" style="left:366px"></span>
    <a style="left:403px">News</a><span class="sep" style="left:486px"></span>
    <a style="left:522px">Productions</a><span class="sep" style="left:671px"></span>
    <a style="left:699px">Investors</a><span class="sep" style="left:833px"></span>
    <a class="contact" style="left:860px">Contact Us</a>
  </nav>

  <section class="panel locations">
    <h2 class="heading serif" style="left:24px;top:24px">OUR LOCATIONS</h2>
    <address class="address" style="font-style:normal">
      2480 Marlow Crest Drive<br>Suite 640<br>Harbor Vale, CA 90412<br>Office: (555) 014-2286
    </address>
    <div class="map">MAP</div>
  </section>

  <div class="hero" role="img" aria-label="Minotaur warrior holding an axe, standing in hellfire"></div>

  <section class="panel form">
    <h2 class="heading caps" style="left:28px;top:22px">CONTACT FORM</h2>
    <span class="label" style="left:24px;top:68px">Enter your name :</span>
    <div class="field" style="top:82px;height:14px"></div>
    <span class="label" style="left:26px;top:104px">Enter your e-mail address :</span>
    <div class="field" style="top:123px;height:14px"></div>
    <span class="label" style="left:28px;top:145px">Enter your message :</span>
    <div class="field" style="left:26px;top:162px;height:112px"></div>
    <div class="btn" style="left:46px">Clear</div>
    <div class="btn" style="left:161px">Send</div>
  </section>

  <section class="panel info">
    <h2 class="heading serif" style="left:24px;top:18px">CONTACT INFO</h2>
    <div class="info-text">
      <p>Emails :<br>Sample Email@ QuillanStudioWorks.com<br>Sample Email@ QuillanStudioWorks.com</p>
      <p>Pagebook :<br>Sample Pagebook</p>
      <p>Chirper :<br>Sample Chirper</p>
    </div>
  </section>

  <div class="social">
    <span>Pagebook</span><span>Circles</span><span>Worklink</span><span>Chirper</span>
  </div>

  <footer class="footer">Quillan Studio © 2014 . Privacy Policy</footer>
</main>
</body>
</html>
```